VENTURE CAPITAL GROUP BUSINESS CARD DESIGN

Venture Capital Group based in SF looking for a bold business card design. No trendy colour explosion, 3D effects etc. Just "simple" optical effects. Works on your brain, keeps your eye focused and sticks to your mind.
Target Market(s)
Technology startups
Industry/Entity Type
Venture Capital
Contact Information for Business Card
DESMOND WHITLAKE
MANAGING PARTNER
187 FENWORTH ST SAN FRANCISCO, CA 94187
415.555.0142 O
415.555.0147 F
415.555.0193 C
desmond@veldtmoorcapital.ventures

```html
<!DOCTYPE html>
<html lang="en">
<head>
<meta charset="utf-8">
<title>Veldtmoor Capital Group – Business Card</title>
<link href="https://fonts.googleapis.com/css2?family=Arimo:wght@400;700&display=swap" rel="stylesheet">
<style>
  :root {
    --green-deep: #0f4a1f;
    --green-main: #1f7a33;
    --green-bright: #34a048;
    --ink: #2b2b2b;
    --grey-text: #7a7a7a;
    --grey-line: #c9c9c9;
    --paper: #ffffff;
    --stage: #e9ebe8;
  }
  * { box-sizing: border-box; margin: 0; padding: 0; }
  html, body {
    width: 1200px; height: 950px; overflow: hidden;
    background: var(--stage);
    font-family: "Arimo", Arial, sans-serif;
  }
  .stage {
    position: relative; width: 1200px; height: 950px;
    display: flex; flex-direction: column; align-items: center; justify-content: center; gap: 60px;
  }
  .card {
    position: relative; width: 700px; height: 400px; overflow: hidden;
    box-shadow: 0 6px 20px rgba(0,0,0,.18);
  }

  /* Back side */
  .card-back {
    background: radial-gradient(ellipse at 45% 40%, var(--green-bright) 0%, var(--green-main) 40%, var(--green-deep) 100%);
    display: flex; flex-direction: column; align-items: center; justify-content: center; gap: 18px;
  }
  .brand-dot {
    width: 96px; height: 96px; border-radius: 50%;
    background: radial-gradient(circle at 40% 35%, #ffffff 0%, #d8d8d8 70%, #b8b8b8 100%);
  }
  .card-back .brand-name {
    color: #e9f2ea; font-size: 40px; font-weight: 400; letter-spacing: 2px;
  }

  /* Front side */
  .card-front { background: linear-gradient(160deg, #ffffff 0%, #f6f6f6 60%, #ececec 100%); }
  .card-front .bands { position: absolute; left: 0; top: 0; }
  .brand-block {
    position: absolute; left: 30px; top: 80px; width: 240px;
    display: flex; flex-direction: column; align-items: center; gap: 14px;
  }
  .brand-block .brand-dot { width: 80px; height: 80px; }
  .brand-block .brand-name {
    color: var(--green-main); font-size: 30px; font-weight: 400; letter-spacing: 1px; line-height: 1;
  }
  .divider {
    position: absolute; left: 290px; top: 55px; width: 1px; height: 265px;
    background: linear-gradient(var(--grey-line), rgba(201,201,201,0));
  }
  .contact { position: absolute; left: 318px; top: 62px; color: var(--ink); }
  .contact .person { color: var(--green-main); font-size: 25px; font-weight: 700; line-height: 1.1; }
  .contact .role { color: var(--grey-text); font-size: 18px; margin-bottom: 12px; }
  .contact .address { font-size: 18px; line-height: 1.2; margin-bottom: 8px; }
  .contact ul { list-style: none; }
  .contact li { display: flex; align-items: center; gap: 10px; font-size: 19px; line-height: 1.4; }
  .contact li svg { width: 18px; height: 18px; flex: none; }
  .website {
    position: absolute; right: 28px; bottom: 16px;
    color: #ffffff; font-size: 23px;
  }
</style>
</head>
<body>
<main class="stage">

  <section class="card card-back" aria-label="Card back">
    <div class="brand-dot"></div>
    <div class="brand-name">VELDTMOOR CAPITAL GROUP</div>
  </section>

  <section class="card card-front" aria-label="Card front">
    <svg class="bands" width="700" height="400" viewBox="0 0 700 400">
      <defs>
        <linearGradient id="band-green" x1="0" x2="1" y1="0" y2="0">
          <stop offset="0" stop-color="#1f7a33"/>
          <stop offset="1" stop-color="#2f9444"/>
        </linearGradient>
        <linearGradient id="band-grey" x1="0" x2="1">
          <stop offset="0" stop-color="#9a9a9a"/>
          <stop offset="1" stop-color="#dedede"/>
        </linearGradient>
      </defs>
      <polygon points="0,378 300,392 300,400 0,400" fill="url(#band-grey)"/>
      <path d="M300,400 C300,370 315,350 360,348 L700,340 L700,400 Z" fill="url(#band-green)"/>
    </svg>

    <div class="brand-block">
      <div class="brand-dot"></div>
      <div class="brand-name">VELDTMOOR</div>
    </div>

    <div class="divider"></div>

    <div class="contact">
      <p class="person">Desmond Whitlake</p>
      <p class="role">Managing Partner</p>
      <p class="address">187 Fenworth ST San Francisco<br>CA 94187</p>
      <ul>
        <li>
          <svg viewBox="0 0 20 20" aria-hidden="true"><path d="M3 7c0-3 14-3 14 0v2h-4V7H7v2H3z M5 10h10l2 7H3z" fill="#1f7a33"/></svg>
          415.555.0142
        </li>
        <li>
          <svg viewBox="0 0 20 20" aria-hidden="true"><rect x="6" y="1" width="8" height="18" rx="1.5" fill="#1f7a33"/><rect x="7.5" y="3.5" width="5" height="10" fill="#fff"/></svg>
          415.555.0193
        </li>
        <li>
          <svg viewBox="0 0 20 20" aria-hidden="true"><rect x="5" y="2" width="10" height="6" fill="#1f7a33"/><rect x="2" y="8" width="16" height="8" rx="1" fill="#1f7a33"/><rect x="5" y="12" width="10" height="6" fill="#fff" stroke="#1f7a33"/></svg>
          415.555.0147
        </li>
        <li>
          <svg viewBox="0 0 20 20" aria-hidden="true"><rect x="2" y="4" width="16" height="12" fill="#1f7a33"/><path d="M2 4l8 7 8-7" fill="none" stroke="#fff" stroke-width="1.5"/></svg>
          desmond@veldtmoorcapital.ventures
        </li>
      </ul>
    </div>

    <p class="website">veldtmoorcapital.ventures</p>
  </section>

</main>
</body>
</html>
```